BUSINESS CARD DESIGN

NAME- DALE VORSKIN
PHONE NUMER - 555- 714-9082
EMAIL- OFFICE@TRV-GROUNDMAKRZ.COM
BACK OF CARD- SPEACIALIZES IN LAND CLEARING, FORESTRY MUCLHING AND EXCAVATION

Contact Information for Business Card

NAME- DALE VORSKIN PHONE NUMER - 555- 714-9082 EMAIL- OFFICE@TRV-GROUNDMAKRZ.COM BACK OF CARD- SPEACIALIZES IN LAND CLEARING , MUCLHING AND EXCAVATION

```html
<!DOCTYPE html>
<html lang="en">
<head>
<meta charset="utf-8">
<title>Business Card – Terravale Ground Makerz</title>
<link rel="stylesheet" href="https://fonts.googleapis.com/css2?family=Montserrat:wght@400;500;700;800&display=swap">
<style>
  :root {
    --ink: #141414;
    --paper: #ffffff;
    --accent: #f6b01a;
    --backdrop: #2b2d30;
    --back-card: #0e0e0e;
    --back-tone: #1a1a1a;
    --text-dark: #1d1d1d;
    --text-soft: #c9c9c9;
  }
  * { margin: 0; padding: 0; box-sizing: border-box; }
  html, body {
    width: 1200px; height: 900px; overflow: hidden;
    background: var(--backdrop);
    font-family: "Montserrat", sans-serif;
  }
  .canvas {
    width: 1200px; height: 900px;
    display: flex; flex-direction: column;
    align-items: center; justify-content: center; gap: 44px;
  }
  .card {
    position: relative;
    width: 700px; height: 400px;
    overflow: hidden;
    box-shadow: 0 12px 30px rgba(0,0,0,.45);
  }
  /* Front */
  .card-front { background: var(--paper); }
  .front-shapes { position: absolute; inset: 0; }
  .brand {
    position: absolute; left: 120px; top: 118px;
    width: 190px;
    display: flex; flex-direction: column; align-items: center; gap: 10px;
    text-align: center;
  }
  .brand-dot {
    width: 54px; height: 54px; border-radius: 50%;
    background: var(--ink);
  }
  .brand-name {
    font-weight: 800; font-size: 17px; letter-spacing: .5px;
    line-height: 1.2; color: var(--ink);
  }
  .brand-phone {
    font-weight: 800; font-size: 11px; letter-spacing: 3px; color: var(--ink);
  }
  .divider {
    position: absolute; left: 330px; top: 112px;
    width: 3px; height: 176px; background: var(--accent);
  }
  .details { position: absolute; left: 352px; top: 110px; }
  .person-name {
    font-weight: 800; font-size: 30px; letter-spacing: .5px;
    color: var(--accent); line-height: 1;
  }
  .person-title {
    margin-top: 8px; font-size: 15px; font-weight: 500; color: var(--text-dark);
  }
  .contact-list { list-style: none; margin-top: 16px; }
  .contact-item {
    display: flex; align-items: center; gap: 10px;
    font-size: 15px; font-weight: 500; color: var(--text-dark);
    line-height: 1; margin-bottom: 11px;
  }
  .contact-icon { width: 14px; height: 14px; flex: none; }
  /* Back */
  .card-back { background: var(--back-card); }
  .back-pattern {
    position: absolute; inset: 0;
    background: radial-gradient(ellipse at 50% 50%, var(--back-tone), var(--back-card) 75%);
  }
  .back-content {
    position: absolute; left: 50%; top: 50%;
    transform: translate(-50%, -50%);
    width: 560px;
    display: flex; flex-direction: column; align-items: center; gap: 22px;
    text-align: center;
  }
  .back-brand { display: flex; align-items: center; gap: 12px; }
  .back-brand-dot { width: 40px; height: 40px; border-radius: 50%; background: var(--paper); }
  .back-brand-name {
    font-weight: 800; font-size: 18px; letter-spacing: .5px;
    color: var(--paper); line-height: 1.2;
  }
  .back-services {
    font-weight: 500; font-size: 13px; letter-spacing: 2px;
    color: var(--text-soft); line-height: 1.6; text-transform: uppercase;
  }
  .back-services strong { color: var(--accent); font-weight: 700; }
</style>
</head>
<body>
<main class="canvas">

  <section class="card card-front" aria-label="Card front">
    <svg class="front-shapes" width="700" height="400" viewBox="0 0 700 400" aria-hidden="true">
      <path d="M0 0 H66 Q0 200 66 400 H0 Z" fill="var(--ink)"/>
      <path d="M92 0 Q30 200 108 400" fill="none" stroke="var(--accent)" stroke-width="5"/>
    </svg>

    <div class="brand">
      <span class="brand-dot" aria-hidden="true"></span>
      <p class="brand-name">TERRAVALE GROUND MAKERZ LLC</p>
      <p class="brand-phone">555-714-9082</p>
    </div>

    <span class="divider" aria-hidden="true"></span>

    <div class="details">
      <h1 class="person-name">DALE VORSKIN</h1>
      <p class="person-title">Managing Director</p>
      <ul class="contact-list">
        <li class="contact-item">
          <svg class="contact-icon" viewBox="0 0 24 24" aria-hidden="true"><path fill="var(--accent)" d="M6.6 10.8a15.1 15.1 0 0 0 6.6 6.6l2.2-2.2a1 1 0 0 1 1-.25 11.4 11.4 0 0 0 3.6.57 1 1 0 0 1 1 1V20a1 1 0 0 1-1 1A17 17 0 0 1 3 4a1 1 0 0 1 1-1h3.5a1 1 0 0 1 1 1c0 1.25.2 2.45.57 3.57a1 1 0 0 1-.25 1z"/></svg>
          555- 714-9082
        </li>
        <li class="contact-item">
          <svg class="contact-icon" viewBox="0 0 24 24" aria-hidden="true"><rect x="2" y="5" width="20" height="14" rx="2" fill="var(--accent)"/><path d="M3 6l9 7 9-7" fill="none" stroke="#fff" stroke-width="2"/></svg>
          OFFICE@TRV-GROUNDMAKRZ.COM
        </li>
        <li class="contact-item">
          <svg class="contact-icon" viewBox="0 0 24 24" aria-hidden="true"><circle cx="12" cy="12" r="10" fill="var(--accent)"/><path d="M2 12h20M12 2c3 3 3 17 0 20M12 2c-3 3-3 17 0 20" fill="none" stroke="#fff" stroke-width="1.5"/></svg>
          WWW.TRV-GROUNDMAKRZ.COM
        </li>
      </ul>
    </div>
  </section>

  <section class="card card-back" aria-label="Card back">
    <div class="back-pattern" role="img" aria-label="Tonal repeating brand pattern in black on black"></div>
    <div class="back-content">
      <div class="back-brand">
        <span class="back-brand-dot" aria-hidden="true"></span>
        <p class="back-brand-name">TERRAVALE</p>
      </div>
      <p class="back-services"><strong>Specializes in</strong><br>Land Clearing, Forestry Mulching and Excavation</p>
    </div>
  </section>

</main>
</body>
</html>
```